Baby Cloth Business Needs a Web Design

We need a web design for a new company that produces and sells baby sleeping bags. We use kelvoTrade (demo.kelvotrade.example) e-commerce software which we need a new design for that represents our products better. We would like to see designs that use simple and clean elements, playful layout with big pictures and emphasis on typography. We already have a logo that is "fresh" apple green so we would like colors that go well with that.
We use the following pages/features:
- Home page (with newsletter, chatterbook link and contact us link)
- Category page (no search needed)
- Product details page (with share)
- User pages (register, login, my account)
- Shopping cart with all its pages (about 6-7)
- Static pages (3 pages: contact us, about us, conditions of use).

We need designs in the form of PSD

Target Market(s)

Primary: mothers 25-45; secondary: women 20-60 who buy it as gift

Industry/Entity Type

Business

Requirements
Must have
• Since the site uses kelvoTrade no other data can be added beside those already exist on site.
Nice to have
• We have photos taken for this site (sample attached) and would be nice to show them in big sizes. We would like to see imaginative, playful elements that appear several places throughout the site. Logo contains a small baby foot which could leave footprints here and there.

We like these sites (and what):
- http://www.pelora.example/13-organic-bamboo-cotton-baby-essentials (simple, nice but too gray)
- http://www.quindeco.example/ (logo placement, menu, background)
- http://www.tervalo.example/
- http://www.brelt.example/website-template/view/html/baby-clothes?originUrl=http%3A%2F%2Fwww.brelt.example%2Fwebsite%2Ftemplates%2Fhtml%2Fonline-shop%2F2&galleryDocIndex=0 (layout, image sizes)
- http://themes.fashion.kel-layouts.example/?isOpen=false&;t_r=true (layout)
Should not have
• We do not use forum, blog, new products, manufacturers, popular tags, polls, search from kelvoTrade.

```html
<!DOCTYPE html>
<html lang="en">
<head>
<meta charset="utf-8">
<title>Snugloo – Home</title>
<link href="https://fonts.googleapis.com/css2?family=PT+Sans:wght@400;700&display=swap" rel="stylesheet">
<style>
:root{
  --dark:#262626;
  --green:#7cc22c;
  --green-dark:#5f9e1c;
  --green-panel:#7db63f;
  --beige:#ece8df;
  --card:#efeded;
  --orange:#f7941d;
  --price:#c4161c;
  --text:#333;
  --muted:#555;
}
*{box-sizing:border-box;margin:0;padding:0}
html,body{width:972px;height:1200px;overflow:hidden;background:#fff}
body{font-family:"PT Sans",sans-serif;color:var(--text)}
.page{position:relative;width:1000px;height:1235px;transform:scale(.972);transform-origin:0 0}
.abs{position:absolute}

.topbar{left:0;top:0;width:1000px;height:44px;background:var(--dark);color:#eee;font-size:11px}
.topbar .welcome{left:72px;top:19px}
.topbar .links{left:428px;top:15px;display:flex;gap:6px;align-items:center}
.topbar .links .sep{color:#888}
.topbar .links .strong{font-size:12.5px}
.select{background:#fff;color:#333;height:19px;border:1px solid #aaa;display:flex;align-items:center;padding:0 6px;font-size:10px;justify-content:space-between}
.select::after{content:"";border:4px solid transparent;border-top:5px solid #333;margin-top:4px}
.currency{left:760px;top:12px;width:62px}
.lang{left:849px;top:12px;width:81px}
.lang .flag{width:20px;height:10px;background:#7a8db8;margin-left:6px;display:inline-block}

.brand{left:72px;top:78px;display:flex;align-items:center;gap:10px}
.brand .mark{width:30px;height:30px;border-radius:50%;background:var(--green)}
.brand .name{font-size:38px;color:var(--green);font-weight:400;line-height:1}
.tagline{left:113px;top:145px;font-size:8px;color:var(--green-dark)}

.nav-shadow{left:50px;top:198px;width:900px;height:22px;background:radial-gradient(ellipse at center top,rgba(0,0,0,.22),rgba(0,0,0,0) 70%)}
.nav{left:70px;top:167px;width:858px;height:40px;background:linear-gradient(#8fd43c,#70b825);border-radius:3px;display:flex;color:#fff;font-size:13px}
.nav a{color:#fff;text-decoration:none;display:flex;align-items:center;justify-content:center;border-right:1px solid #69ad23;box-shadow:1px 0 0 #97da4c}
.nav a:last-child{border:0;box-shadow:none}

.hero{left:72px;top:227px;width:856px;height:365px;background:
  radial-gradient(ellipse 200px 230px at 430px 190px,#e9c6a8 0,#d8a98a 55%,rgba(216,169,138,0) 100%),
  radial-gradient(ellipse 260px 110px at 540px 380px,#7fd3da 0,#5bbfc8 60%,rgba(91,191,200,0) 100%),
  linear-gradient(90deg,#f2f2f0 0,#ecebe8 20%,#a5643a 34%,#b8753f 66%,#e8e6e2 82%,#efeeec 100%)}
.dots{left:874px;top:572px;display:flex;gap:2px}
.dots span{width:9px;height:9px;border-radius:50%;background:#333;border:1px solid #fff}
.dots span:first-child{background:#fff;border-color:#555}

.promo{top:625px;width:265px;height:164px;background:var(--beige);border:1px solid #e0dcd2}
.promo h2{position:absolute;left:14px;top:13px;font-size:17px;font-weight:400;color:#222}
.promo .photo{position:absolute;left:15px;top:45px;width:118px;height:104px}
.promo p{position:absolute;left:150px;top:49px;width:105px;font-size:11px;line-height:18px;color:var(--muted)}
.btn-read{position:absolute;left:152px;top:121px;width:93px;height:25px;background:var(--orange);color:#fff;font-size:11px;font-weight:700;display:flex;align-items:center;padding-left:6px;gap:8px}
.btn-read i{width:17px;height:17px;border-radius:50%;background:#fff;display:flex;align-items:center;justify-content:center}

.newsletter{left:664px;top:625px;width:265px;height:164px;background:var(--green-panel);color:#fff}
.newsletter h2{position:absolute;left:14px;top:13px;font-size:17px;font-weight:400}
.newsletter p{position:absolute;left:15px;top:42px;width:245px;font-size:11px;line-height:18px}
.newsletter .email{position:absolute;left:15px;top:88px;width:239px;height:24px;background:#fff;color:#888;font-style:italic;font-size:11px;padding:5px 10px}
.newsletter .submit{position:absolute;left:180px;top:127px;width:74px;height:27px;background:linear-gradient(#fafafa,#dcdcdc);color:#444;font-size:13px;display:flex;align-items:center;justify-content:center}

.section-title{left:70px;top:817px;font-size:17px;font-weight:400;color:var(--green-dark)}
.card{top:861px;width:182px;height:261px;background:var(--card)}
.card .photo{position:absolute;left:22px;top:14px;width:130px;height:118px;border-radius:45% 45% 30% 30%}
.card .title{position:absolute;left:23px;top:147px;font-size:13px;color:#444}
.card .price{position:absolute;left:23px;top:182px;font-size:13px;color:var(--price)}
.card .cart{position:absolute;left:24px;top:212px;width:26px;height:25px;background:#333;display:flex;align-items:center;justify-content:center}
.card .details{position:absolute;left:68px;top:212px;width:66px;height:26px;background:linear-gradient(#8a8a8a,#4c4c4c);color:#fff;font-size:13px;display:flex;align-items:center;justify-content:center}

.footer{left:0;top:1161px;width:1000px;height:74px;background:var(--dark);color:#eee;font-size:11px}
.footer .copy{position:absolute;left:71px;top:27px}
.footer .social{position:absolute;left:770px;top:28px;display:flex;gap:10px;font-size:9px;color:#ddd}
</style>
</head>
<body>
<div class="page">

  <header>
    <div class="abs topbar">
      <div class="abs welcome">Welcome, ( log in)</div>
      <div class="abs links">
        <span>Cart : (0) items</span><span class="sep">|</span>
        <span class="strong">Your Account</span><span class="sep">|</span>
        <span>Customer Support</span><span class="sep">|</span>
        <span>Currency :</span>
      </div>
      <div class="abs select currency">Dollar</div>
      <div class="abs select lang"><span>ENG<span class="flag"></span></span></div>
    </div>

    <div class="abs brand"><span class="mark"></span><span class="name">Snugloo</span></div>
    <div class="abs tagline">smart sleeping bag for babies and kids</div>

    <div class="abs nav-shadow"></div>
    <nav class="abs nav">
      <a style="width:96px">HOME</a>
      <a style="width:122px">ABOUT US</a>
      <a style="width:115px">SERVICES</a>
      <a style="width:129px">PRODUCTS</a>
      <a style="width:114px">NANNIES</a>
      <a style="width:165px">SPECIAL OFFERSE</a>
      <a style="width:117px">CONTACT</a>
    </nav>
  </header>

  <main>
    <div class="abs hero" role="img" aria-label="Smiling toddler in a spotted blue top sitting on a wooden chair"></div>
    <div class="abs dots"><span></span><span></span><span></span><span></span></div>

    <section class="abs promo" style="left:72px">
      <h2>PARENTS - GET STARTED</h2>
      <div class="photo" role="img" aria-label="Father carrying his laughing daughter" style="background:linear-gradient(135deg,#9cc4e0,#d9a27c 55%,#5d8fb8)"></div>
      <p>Post a job today &amp; meet experienced sitters in your area.</p>
      <div class="btn-read">READ NOW <i><svg width="9" height="9" viewBox="0 0 9 9"><path d="M1 4.5h6M4.5 1.5l3 3-3 3" stroke="#f7941d" stroke-width="1.6" fill="none"/></svg></i></div>
    </section>

    <section class="abs promo" style="left:363px">
      <h2 style="top:15px">NANNIES - GET STARTED</h2>
      <div class="photo" role="img" aria-label="Mother cuddling a smiling baby" style="background:linear-gradient(135deg,#c88c66,#f0d7c4 55%,#f7f2ee)"></div>
      <p style="top:51px">Post a job today &amp; meet experienced sitters in your area.</p>
      <div class="btn-read" style="top:123px">READ NOW <i><svg width="9" height="9" viewBox="0 0 9 9"><path d="M1 4.5h6M4.5 1.5l3 3-3 3" stroke="#f7941d" stroke-width="1.6" fill="none"/></svg></i></div>
    </section>

    <section class="abs newsletter">
      <h2>NEWSLETTER SIGNUP</h2>
      <p>Sign up your Newsletter for Our bi - weekly New sletter about our products</p>
      <div class="email">Enter your Email Id</div>
      <div class="submit">SUBMIT</div>
    </section>

    <h2 class="abs section-title">Our Collections</h2>

    <article class="abs card" style="left:71px">
      <div class="photo" role="img" aria-label="Baby bean bag seat with patterned base" style="background:linear-gradient(#c9dff0 0,#9fc2dd 40%,#4a3a2a 60%,#2e2418)"></div>
      <div class="title">Set ipsum dolor sit amet</div><div class="price">$10.97</div>
      <div class="cart"><svg width="14" height="12" viewBox="0 0 14 12"><path d="M0 1h3l2 7h7l2-5H4" stroke="#fff" stroke-width="1.5" fill="none"/><circle cx="6" cy="10.5" r="1.2" fill="#fff"/><circle cx="11" cy="10.5" r="1.2" fill="#fff"/></svg></div>
      <div class="details">DETAILS</div>
    </article>

    <article class="abs card" style="left:295px">
      <div class="photo" role="img" aria-label="Colourful flower-shaped baby play mat" style="background:radial-gradient(circle,#f2e3d4 0,#f3c64a 35%,#8fb43c 60%,#e07a3a 80%,rgba(239,237,237,0) 95%)"></div>
      <div class="title">Set ipsum dolor sit amet</div><div class="price">$10.97</div>
      <div class="cart"><svg width="14" height="12" viewBox="0 0 14 12"><path d="M0 1h3l2 7h7l2-5H4" stroke="#fff" stroke-width="1.5" fill="none"/><circle cx="6" cy="10.5" r="1.2" fill="#fff"/><circle cx="11" cy="10.5" r="1.2" fill="#fff"/></svg></div>
      <div class="details">DETAILS</div>
    </article>

    <article class="abs card" style="left:522px">
      <div class="photo" role="img" aria-label="Pink corduroy bean bag" style="background:radial-gradient(ellipse at 45% 40%,#f6a9c6,#e2679a 70%,#c84f80)"></div>
      <div class="title">Set ipsum dolor sit amet</div><div class="price">$10.97</div>
      <div class="cart"><svg width="14" height="12" viewBox="0 0 14 12"><path d="M0 1h3l2 7h7l2-5H4" stroke="#fff" stroke-width="1.5" fill="none"/><circle cx="6" cy="10.5" r="1.2" fill="#fff"/><circle cx="11" cy="10.5" r="1.2" fill="#fff"/></svg></div>
      <div class="details">DETAILS</div>
    </article>

    <article class="abs card" style="left:746px">
      <div class="photo" role="img" aria-label="Purple corduroy bean bag" style="background:radial-gradient(ellipse at 45% 40%,#9d92de,#6e5fc4 70%,#5547a6)"></div>
      <div class="title">Set ipsum dolor sit amet</div><div class="price">$10.97</div>
      <div class="cart"><svg width="14" height="12" viewBox="0 0 14 12"><path d="M0 1h3l2 7h7l2-5H4" stroke="#fff" stroke-width="1.5" fill="none"/><circle cx="6" cy="10.5" r="1.2" fill="#fff"/><circle cx="11" cy="10.5" r="1.2" fill="#fff"/></svg></div>
      <div class="details">DETAILS</div>
    </article>
  </main>

  <footer class="abs footer">
    <div class="copy">Copyrights 2013. Snugloo. All Rights Reserved.</div>
    <div class="social"><span>chatterbook</span><span>chirpline</span><span>linkfolio</span><span>orbitplus</span></div>
  </footer>

</div>
</body>
</html>
```